Flyer for the Radiant Harvest Worship Day

I am looking to create a flyer for a one day prayer retreat our church is organizing.
This flyer will be posted on social media, websites and will also be printed so it can be mailed to people.
I am looking for something professional, with good use of our logo and band colors (logo colors).
I am counting on the designer's skill, creativity, art and knowledge of media communication to produce a flyer that will effectively and quickly convey the message we are trying to spread.
CONTENT OF THE FLYER:
Event title: Radiant Harvest Worship Day
Date: Tuesday July 2nd, 2019
Time: 11:00AM - 7:00PM
Belmora Hotel, 4875 Wexley Avenue, Portland, Maine 04102 (Room: Juniper)
Event Key words to highlight what the event is about: Prayer, Sharing the Word, Panel discussion, prophecy, Impartation.
Key phrases:
A one day prayer retreat.
Jesus Chris is Lord
Contact info:
www.tolvex.org
Phone: 207 555 3184
Email: contact@brookhavenfold.org

```html
<!DOCTYPE html>
<html lang="en">
<head>
<meta charset="utf-8">
<title>Radiant Harvest Worship Day</title>
<link rel="stylesheet" href="https://fonts.googleapis.com/css2?family=Poppins:wght@600;700&family=Roboto:wght@700&family=Roboto+Condensed:wght@400;700&display=swap">
<style>
  :root {
    --navy: #12365c;
    --orange: #f7941d;
    --cream: #fdf1dd;
    --cream-deep: #f6dfbd;
    --maroon: #6a2417;
    --ink-blue: #1d3d63;
    --white: #ffffff;
  }
  * { margin: 0; padding: 0; box-sizing: border-box; }
  html, body { width: 848px; height: 1200px; overflow: hidden; background: #ffffff; }
  .flyer {
    position: relative;
    width: 848px;
    height: 1200px;
    overflow: hidden;
    font-family: "Roboto Condensed", sans-serif;
  }
  .sky-backdrop {
    position: absolute; inset: 0;
    background:
      radial-gradient(ellipse 70% 40% at 75% 38%, rgba(255,236,190,0.85), rgba(255,236,190,0) 70%),
      linear-gradient(180deg, #4a1d0c 0%, #a8501a 12%, #e4902f 32%, #f1b24e 48%, #e69a36 62%, #8c4014 80%, #2a1206 92%, #120703 100%);
  }
  .header-band {
    position: absolute; left: 35px; top: 45px; width: 797px; height: 176px;
    background: var(--cream);
    display: flex;
  }
  .brand-block {
    width: 179px; height: 100%;
    background: var(--navy);
    display: flex; align-items: center; justify-content: center; gap: 8px;
  }
  .brand-dot { width: 12px; height: 12px; border-radius: 50%; background: var(--orange); }
  .brand-name {
    font-family: "Roboto Condensed", sans-serif; font-weight: 400;
    color: var(--white); font-size: 34px; letter-spacing: 1px;
  }
  .event-title {
    flex: 1; text-align: center; padding-top: 24px;
  }
  .event-title h1 {
    font-family: "Roboto", sans-serif; font-weight: 700;
    color: var(--orange); font-size: 60px; line-height: 1;
    letter-spacing: -0.5px;
  }
  .event-title .subtitle {
    font-family: "Roboto Condensed", sans-serif; font-weight: 700;
    color: #c2561c; font-size: 25px; margin-top: 6px; letter-spacing: 0.3px;
  }
  .accent-strip { width: 13px; height: 100%; background: var(--orange); }
  .tagline {
    position: absolute; left: 70px; top: 262px;
    font-family: "Poppins", sans-serif; font-weight: 700;
    color: var(--maroon); font-size: 46px; letter-spacing: -0.3px;
  }
  .info-block {
    position: absolute; right: 85px; width: 206px; text-align: right;
    color: var(--ink-blue); font-size: 19px; line-height: 27px;
  }
  .info-block h2 {
    font-weight: 700; color: var(--maroon); font-size: 22px;
    padding-bottom: 6px; border-bottom: 3px solid var(--orange);
    margin-bottom: 10px; line-height: 1.1;
  }
  .info-date { top: 340px; }
  .info-location { top: 490px; }
  .keywords {
    position: absolute; right: 87px; top: 695px;
    display: flex; flex-direction: column; align-items: flex-end; gap: 9px;
  }
  .keyword {
    font-family: "Roboto Condensed", sans-serif; font-weight: 400;
    color: var(--maroon); font-size: 58px; line-height: 66px;
    padding: 0 10px 0 16px; background: rgba(253,241,221,0.93);
  }
  .keyword:nth-child(even) { background: rgba(246,223,189,0.93); }
  .contact {
    position: absolute; right: 87px; top: 1122px; text-align: right;
    font-family: "Poppins", sans-serif; font-weight: 600;
    color: var(--white); font-size: 17.5px; line-height: 30px;
  }
  .contact .divider { margin: 0 10px; }
</style>
</head>
<body>
<main class="flyer">
  <div class="sky-backdrop" role="img" aria-label="Sunset sky in orange and gold with three dark cross silhouettes on a hill"></div>

  <header class="header-band">
    <div class="brand-block">
      <span class="brand-dot"></span>
      <span class="brand-name">TOLVEX</span>
    </div>
    <div class="event-title">
      <h1>Radiant Harvest</h1>
      <p class="subtitle">WORSHIP DAY</p>
    </div>
    <div class="accent-strip"></div>
  </header>

  <p class="tagline">A One Day Prayer Retreat</p>

  <section class="info-block info-date">
    <h2>DATE &amp; TIME</h2>
    <p>Tuesday July 2nd, 2019<br>11:00AM - 7:00PM</p>
  </section>

  <section class="info-block info-location">
    <h2>LOCATION</h2>
    <p>Belmora Hotel,<br>4875 Wexley Avenue,<br>Portland, Maine 04102<br>(Room: Juniper)</p>
  </section>

  <ul class="keywords">
    <li class="keyword">Prayer</li>
    <li class="keyword">Sharing the Word</li>
    <li class="keyword">Panel Discussion</li>
    <li class="keyword">Prophecy</li>
    <li class="keyword">Impartation</li>
  </ul>

  <footer class="contact">
    <p>Phone: 207 555 3184<span class="divider">|</span>Email: contact@brookhavenfold.org</p>
    <p>www.tolvex.org</p>
  </footer>
</main>
</body>
</html>
```